Coastline Premier Retreats Business Card Design

Design a business card for Coastline Premier Retreats. Look at the website for colors and reference. Card should have logo, name, title, office number, mobile number, email, URL and a tagline like, "Luxury Hotel & Resort Email Marketing" (This might change).

https://www.coastlinepremierretreats.example

The rest I will leave up to your imagination.

Contact Information for Business Card

Logo, name, title, office number, mobile number, email, URL and a tagline like, "Luxury Hotel & Resort Email Marketing" (This might change).

```html
<!DOCTYPE html>
<html lang="en">
<head>
<meta charset="utf-8">
<title>Coastline Premier Retreats – Business Card</title>
<link href="https://fonts.googleapis.com/css2?family=Montserrat:wght@400;500;700;800&display=swap" rel="stylesheet">
<style>
  :root {
    --backdrop: #2b2b2b;
    --card: #1c1c1c;
    --orange: #f07c1b;
    --white: #ffffff;
    --soft-white: #e9e9e9;
  }
  * { box-sizing: border-box; margin: 0; padding: 0; }
  html, body {
    width: 1200px; height: 915px; overflow: hidden;
    background: var(--backdrop);
    font-family: "Montserrat", Arial, sans-serif;
  }
  .canvas {
    width: 1200px; height: 915px;
    display: flex; flex-direction: column;
    align-items: center; justify-content: center; gap: 46px;
  }
  .card {
    position: relative;
    width: 660px; height: 377px;
    background: var(--card);
    box-shadow: 0 10px 30px rgba(0,0,0,.45);
    overflow: hidden;
  }
  .brand-name {
    color: var(--white);
    font-weight: 800;
    text-transform: uppercase;
    letter-spacing: 1px;
    line-height: 1.1;
  }

  /* Front */
  .card-front {
    display: flex; flex-direction: column;
    align-items: center; justify-content: center;
  }
  .card-front .brand-name { font-size: 30px; text-align: center; }
  .tagline {
    margin-top: 58px;
    color: var(--orange);
    font-size: 17px; font-weight: 500;
    letter-spacing: .3px;
  }

  /* Back */
  .card-back .brand-name {
    position: absolute; left: 44px; top: 70px;
    font-size: 22px; width: 300px;
  }
  .accent-block {
    position: absolute; right: 0; top: 58px;
    width: 26px; height: 40px;
    background: var(--orange);
  }
  .person {
    position: absolute; right: 46px; top: 56px;
    text-align: right;
  }
  .person-name {
    color: var(--orange);
    font-size: 28px; font-weight: 800;
    letter-spacing: 1px; text-transform: uppercase;
  }
  .person-title {
    color: var(--white);
    font-size: 14px; font-weight: 500;
    margin-top: 2px;
  }
  .divider {
    position: absolute; left: 44px; right: 170px; top: 208px;
    height: 1px; background: var(--orange);
  }
  .contact-list {
    position: absolute; left: 44px; top: 232px;
    list-style: none;
  }
  .contact-list li {
    display: flex; align-items: center; gap: 10px;
    color: var(--soft-white);
    font-size: 17px; font-weight: 400;
    line-height: 27px;
  }
  .contact-list svg { width: 14px; height: 14px; fill: var(--orange); flex: none; }
</style>
</head>
<body>
<main class="canvas">

  <section class="card card-front">
    <div class="brand-name">Coastline Premier Retreats</div>
    <p class="tagline">Luxury Hotel &amp; Resort Email Marketing</p>
  </section>

  <section class="card card-back">
    <div class="brand-name">Coastline Premier Retreats</div>

    <div class="accent-block"></div>
    <div class="person">
      <div class="person-name">Daniel Reyes</div>
      <div class="person-title">Managing Director</div>
    </div>

    <div class="divider"></div>

    <ul class="contact-list">
      <li>
        <svg viewBox="0 0 14 14" aria-hidden="true"><path d="M4 0h6a1.5 1.5 0 0 1 1.5 1.5v11A1.5 1.5 0 0 1 10 14H4a1.5 1.5 0 0 1-1.5-1.5v-11A1.5 1.5 0 0 1 4 0zm0 1.8v9.4h6V1.8zm3 10.2a.8.8 0 1 0 0 1.6.8.8 0 0 0 0-1.6z"/></svg>
        555.010.4821
      </li>
      <li>
        <svg viewBox="0 0 14 14" aria-hidden="true"><path d="M3 .5l2.3 2.6-1.2 1.8c.9 2 2.6 3.8 4.9 4.9l1.8-1.2 2.7 2.3-1.3 2.3C6.3 13.2.8 7.7.7 1.7z"/></svg>
        555.010.6300
      </li>
      <li>
        <svg viewBox="0 0 14 14" aria-hidden="true"><path d="M0 2.5h14v9H0zm1.4 1.2L7 7.8l5.6-4.1z"/></svg>
        dreyes@coastlinepremierretreats.example
      </li>
      <li>
        <svg viewBox="0 0 14 14" aria-hidden="true"><path d="M7 0a7 7 0 1 0 0 14A7 7 0 0 0 7 0zm0 1.4c.8 0 1.7 1.6 2 4.1H5c.3-2.5 1.2-4.1 2-4.1zM1.5 6.3h2.7c0 .5 0 1 .1 1.4H1.5a5.6 5.6 0 0 1 0-1.4zm8.3 0h2.7a5.6 5.6 0 0 1 0 1.4H9.7zM5 8.5h4c-.3 2.5-1.2 4.1-2 4.1s-1.7-1.6-2-4.1z"/></svg>
        www.coastlinepremierretreats.example
      </li>
    </ul>
  </section>

</main>
</body>
</html>
```